Business Cards Needed for Innovative Healthcare Marketing Company

We are a marketing company focused on healthcare. Our company is all about rebranding yourself renewing your image and generating results. The phoenix stands for "reborn" or "rising" which we provide new brands for our clients we take their old brands and renew it with creativity and innovation. I am looking for a business card with color dimension. I have attached an example of a card I think has the look and feel of what I am trying to accomplish. I like that the card example has black and grey font colors, I like the font placement and the small logo, I really like the use of the colors on the right those are the colors of my logo. My logo is phoenix so maybe incorporating flames similar to that design. I would like the back a solid color maybe red with an opaque version of the logo and website. As a marketing company I am always open to creative liberty!

Target Market(s)

Doctors and business professionals.

Industry/Entity Type

Marketing

Contact Information for Business Card

Valcorne Health Care Marketing
Marla Tenwick- CEO
#(512)638-2974
email-marla@valcorne.com
website- valcorne.com

Font styles to use
Sans Serif

Colors
ec1f27
f37122
ffc214
fbed22
fbf289
f04a50

Requirements
Must have
• The logo and required information
Nice to have
• icons by the information
Should not have
• child like font

```html
<!DOCTYPE html>
<html lang="en">
<head>
<meta charset="utf-8">
<title>Valcorne Health Care Marketing – Business Cards</title>
<link rel="stylesheet" href="https://fonts.googleapis.com/css2?family=Open+Sans:wght@300;400;600;700&display=swap">
<style>
  :root {
    --backdrop: #ece8e3;
    --card-white: #ffffff;
    --brand-red: #a52424;
    --brand-orange: #ef8a1f;
    --flame-light: #f6a23a;
    --flame-deep: #b1271f;
    --back-top: #f08a2a;
    --back-bottom: #b3331f;
    --ink-dark: #333333;
    --ink-white: #ffffff;
    --shadow: rgba(60, 40, 20, 0.28);
  }
  * { box-sizing: border-box; margin: 0; padding: 0; }
  html, body { width: 1200px; height: 900px; overflow: hidden; }
  body {
    background: var(--backdrop);
    font-family: "Open Sans", Arial, sans-serif;
    position: relative;
  }
  .card {
    position: absolute;
    width: 560px;
    height: 320px;
    border-radius: 3px;
    overflow: hidden;
    box-shadow: 0 14px 30px var(--shadow);
  }

  /* Back of card */
  .card-back {
    left: 150px;
    top: 150px;
    background: linear-gradient(180deg, var(--back-top) 0%, var(--back-bottom) 100%);
  }
  .card-back .flame-art {
    position: absolute;
    left: 10px;
    top: 10px;
    width: 190px;
    height: 300px;
    border-radius: 60% 40% 30% 70% / 45% 40% 60% 55%;
    background: linear-gradient(160deg, rgba(165, 36, 36, 0.55) 0%, rgba(246, 162, 58, 0.75) 100%);
  }
  .card-back .brand-name {
    position: absolute;
    left: 250px;
    top: 128px;
    width: 280px;
    font-weight: 300;
    font-size: 27px;
    line-height: 1.2;
    color: var(--ink-white);
    letter-spacing: 0.5px;
  }

  /* Front of card */
  .card-front {
    left: 480px;
    top: 400px;
    background: var(--card-white);
  }
  .card-front .bands { position: absolute; inset: 0; }
  .card-front .flame-art {
    position: absolute;
    right: 0;
    top: 0;
    width: 190px;
    height: 250px;
    border-radius: 55% 0 40% 60% / 50% 0 55% 50%;
    background: linear-gradient(200deg, var(--flame-deep) 0%, var(--flame-light) 100%);
  }
  .card-front .brand-name {
    position: absolute;
    left: 40px;
    top: 36px;
    width: 300px;
    font-weight: 300;
    font-size: 26px;
    line-height: 1.2;
    color: var(--brand-red);
    letter-spacing: 0.5px;
  }
  .card-front .person {
    position: absolute;
    left: 30px;
    top: 128px;
  }
  .person-name {
    font-weight: 700;
    font-size: 19px;
    color: var(--brand-red);
  }
  .person-role {
    font-weight: 400;
    font-size: 14px;
    color: var(--ink-dark);
  }
  .contact-list {
    position: absolute;
    left: 50px;
    top: 222px;
    list-style: none;
  }
  .contact-list li {
    display: flex;
    align-items: center;
    gap: 9px;
    font-size: 16px;
    color: var(--ink-white);
    line-height: 26px;
  }
  .contact-list svg { width: 12px; height: 12px; fill: var(--ink-white); }
</style>
</head>
<body>

  <section class="card card-back" aria-label="Card back">
    <div class="flame-art" role="img" aria-label="Rising phoenix illustration in flame tones"></div>
    <p class="brand-name">Valcorne Health Care Marketing</p>
  </section>

  <section class="card card-front" aria-label="Card front">
    <svg class="bands" viewBox="0 0 560 320" preserveAspectRatio="none" aria-hidden="true">
      <polygon points="0,178 420,152 424,161 0,188" fill="var(--brand-orange)"/>
      <polygon points="0,198 430,170 560,268 560,320 0,320" fill="var(--brand-red)"/>
    </svg>
    <div class="flame-art" role="img" aria-label="Rising phoenix illustration in red and orange"></div>
    <p class="brand-name">Valcorne Health Care Marketing</p>
    <div class="person">
      <p class="person-name">Marla Tenwick</p>
      <p class="person-role">CEO</p>
    </div>
    <ul class="contact-list">
      <li>
        <svg viewBox="0 0 16 16" aria-hidden="true"><path d="M3 1h3l1.5 4-2 1.2a9 9 0 0 0 4.3 4.3L11 8.5l4 1.5v3a2 2 0 0 1-2 2A12 12 0 0 1 1 3a2 2 0 0 1 2-2z"/></svg>
        (512)638-2974
      </li>
      <li>
        <svg viewBox="0 0 16 16" aria-hidden="true"><path d="M1 3h14v10H1z M1 3l7 6 7-6" fill="none" stroke="#fff" stroke-width="1.6"/></svg>
        marla@valcorne.com
      </li>
      <li>
        <svg viewBox="0 0 16 16" aria-hidden="true"><circle cx="8" cy="8" r="7"/></svg>
        valcorne.com
      </li>
    </ul>
  </section>

</body>
</html>
```